Webpage for co-working space for tech startups

We have an established co-working space in Aalborg Denmark where we have around 30 companies sharing office space. We are starting a new chapter for us and would like to have a new graphical image - new logo and new webpage, but keep the same name. The webpage should be professional, but also "fun", not too serious. We are all about working hard on our companies, but also taking some time off in between and being social and having fun. We are not corporate, but want to project the image that we are serious about what we do.

We currently have a black/red logo (see www.hivedesk.dk or test.hivedesk.dk), but are interesting in having a new logo design, so colour can be chosen freely. Currently our logo is a big HIVE and a little desk underneath the HIVE. The new logo will be one word "hivedesk" with a small logo before or on top.

If we can make a good webpage for this project, then I have a second more simple project which is also a small single page wordpress site which I would also like to have made.

Target Market(s)

tech startups - relatively new companies, typically younger people 20-35 with a tech background - business or programming, preferably both

Industry/Entity Type

HIVE

Logo Text

hivedesk

Coding

Coded - Design and coding required

Number of Pages Required

4 page

Font styles to use
Sans Serif

Colors

Designer to choose colors to be used in the design.

Requirements
Must have
• Wordpress CMS.
• Mobile and PC optimized
• 2 languages - English and Danish
• Four sections, could be four pages, or four sections of a single page.
• "Home", "Residents", "Our Working Space", "Our Event Space"
• Footer of page or pages should have contact information.
• "Home" has some information about who we are and what we do
• "Residents" has a list of all our residents - it should be possible to easily add and removed new / old residents - See one example here: http://test.hivedesk.dk/en_GB/beboere/ or another example here: http://www.hivedesk.dk/beboere/ - one of our colleagues http://pilotbarn.dk/startups/ or another one of our colleagues http://www.brightkelpyard.dk/residents/
• "Our working space" will have a description of our building, a map of where it is and a bunch of photos which show the different offices, meeting rooms and people working
• "Our events space" will have a description of our event spaces, details of cost + different arrangments of furniture, and lots of photos of events, see here for an example http://www.hivedesk.dk/lej-vores-lokaler/
• Our current webpage - www.hivedesk.dk was put together very quickly and has not really been optimized. We started a new webpage test.hivedesk.dk, but it was never really finished.
• We are looking for a simple webpage, not too much going on. Examples of some of our colleagues in the business http://pilotbarn.dk/, http://www.brightkelpyard.dk/,
Nice to have
• http://www.brightkelpyard.dk/ is a really good template for us. If we can get something like this, we are happy.

```html
<!DOCTYPE html>
<html lang="en">
<head>
<meta charset="utf-8">
<title>NorvelHub – Our Event Space</title>
<link rel="stylesheet" href="https://fonts.googleapis.com/css2?family=Fira+Sans+Condensed:wght@400;500;600;700&family=Montserrat:wght@400;500;600;700&display=swap">
<style>
:root{
  --red:#b5121b;
  --red-deep:#a90e16;
  --ink:#1f1f1f;
  --grey-text:#555;
  --band:#f1f1f1;
  --black:#0b0b0b;
  --white:#fff;
}
*{margin:0;padding:0;box-sizing:border-box}
html,body{width:674px;height:1200px;overflow:hidden;background:var(--white)}
body{position:relative;font-family:"Fira Sans Condensed",sans-serif;color:var(--ink)}
.abs{position:absolute}

/* hero */
.hero{left:0;top:0;width:674px;height:166px;background:radial-gradient(ellipse at 45% 70%,#4a3f3a 0%,#2a2523 45%,#151312 100%)}
.hero-shade{left:0;top:0;width:674px;height:166px;background:rgba(0,0,0,.35)}
.brand{font-family:"Montserrat",sans-serif;font-weight:700;color:var(--white);letter-spacing:.6px;white-space:nowrap}
.brand-top{left:55px;top:20px;font-size:12.5px;line-height:16px}
.main-nav{right:58px;top:20px;display:flex;align-items:center;gap:15px;font-size:9.4px;line-height:16px;color:var(--white);font-weight:500}
.lang{display:flex;align-items:center;gap:5px}
.lang-flag{width:22px;height:15px;background:#1d3b8a;border:1px solid #fff}
.hero-rule{left:55px;top:53px;width:563px;height:1px;background:rgba(255,255,255,.45)}
.hero-title{left:0;width:674px;top:98px;text-align:center;color:var(--white);font-weight:700;font-size:34px;letter-spacing:1.2px}

/* intro */
.section-title{left:0;width:674px;top:204px;text-align:center;color:var(--red);font-weight:700;font-size:19.5px;letter-spacing:.4px}
.title-rule{left:303px;top:238px;width:68px;height:2px;background:var(--red)}
.intro{left:60px;width:554px;top:261px;text-align:center;font-size:8.6px;line-height:12.5px;color:var(--grey-text)}
.tagline{left:0;width:674px;top:315px;text-align:center;color:var(--red);font-size:9.8px;font-weight:500}

/* image frame */
.frame-band{left:63px;top:356px;width:548px;height:263px;background:var(--red)}
.event-photo{left:55px;top:367px;width:563px;height:241px;background:linear-gradient(180deg,#e9e4dc 0%,#d9cfc4 45%,#c59d78 75%,#b58a63 100%)}

/* prices */
.prices-title{left:55px;top:654px;color:var(--red);font-weight:500;font-size:15.5px}
.prices-rule{left:55px;top:678px;width:61px;height:1px;background:var(--red)}
.price-list{left:55px;top:695px;list-style:none;font-size:8.6px;color:var(--ink)}
.price-list li{display:flex;align-items:center;gap:8px;height:25px}
.price-list svg{width:8px;height:8px;flex:none}
.quote{left:55px;top:811px;display:flex;align-items:center;gap:9px;font-size:9.8px;font-weight:500}
.quote-phone{color:var(--red)}

/* cta band */
.cta-band{left:0;top:868px;width:674px;height:53px;background:var(--band)}
.btn-home{left:281px;top:883px;width:112px;height:27px;border:1.5px solid var(--red);color:var(--red);font-weight:600;font-size:9.6px;letter-spacing:.6px;display:flex;align-items:center;justify-content:center}

/* contact footer */
.contact{left:0;top:921px;width:674px;height:153px;background:linear-gradient(180deg,#b8121a,#a90e16)}
.contact-heading{left:55px;top:962px;color:var(--white);font-family:"Montserrat",sans-serif;font-weight:600;font-size:12px;line-height:18px}
.btn-info{left:55px;top:1010px;width:92px;height:27px;border:1.5px solid var(--white);color:var(--white);font-family:"Montserrat",sans-serif;font-weight:600;font-size:8.6px;letter-spacing:.4px;display:flex;align-items:center;justify-content:center}
.contact-divider{left:277px;top:947px;width:1px;height:103px;background:rgba(255,255,255,.55)}
.col-title{color:var(--white);font-family:"Montserrat",sans-serif;font-weight:600;font-size:9.4px}
.visit-title{left:311px;top:960px}
.hours-title{left:497px;top:960px}
.visit-list{left:298px;top:984px;list-style:none;color:var(--white);font-family:"Montserrat",sans-serif;font-size:6.9px;line-height:12.3px}
.visit-list li{display:flex;gap:10px;margin-bottom:7px}
.visit-list svg{width:8px;height:8px;flex:none;margin-top:2px}
.hours-text{left:497px;top:984px;color:var(--white);font-family:"Montserrat",sans-serif;font-size:6.9px;line-height:12.5px}

/* base footer */
.base{left:0;top:1074px;width:674px;height:126px;background:var(--black)}
.foot-nav{left:55px;top:1118px;display:flex;color:var(--white);font-family:"Montserrat",sans-serif;font-size:7.9px;font-weight:500}
.foot-nav span+span::before{content:"|";margin:0 10px}
.foot-rule{left:55px;top:1136px;width:333px;height:1px;background:rgba(255,255,255,.4)}
.copyright{left:55px;top:1143px;color:var(--white);font-family:"Montserrat",sans-serif;font-size:7.2px;font-weight:500}
.brand-foot{right:56px;top:1110px;font-size:15px;line-height:18px}
.social{left:515px;top:1141px;display:flex;gap:5px}
.social span{width:16px;height:16px;border-radius:50%;background:#6d6d6d}
</style>
</head>
<body>

<header>
  <div class="abs hero" role="img" aria-label="Photo of a smiling woman working at a desk in a warmly lit office"></div>
  <div class="abs hero-shade"></div>
  <div class="abs brand brand-top">NORVELHUB</div>
  <nav class="abs main-nav">
    <span>Home</span><span>Residents</span><span>Our Working Space</span><span>Our Event Space</span><span>Contact</span>
    <span class="lang"><span class="lang-flag" role="img" aria-label="English language flag"></span>Eng ▾</span>
  </nav>
  <div class="abs hero-rule"></div>
  <h1 class="abs hero-title">OUR EVENT SPACE</h1>
</header>

<main>
  <h2 class="abs section-title">YOUR EVENT AT NORVELHUB</h2>
  <div class="abs title-rule"></div>
  <p class="abs intro">Should you rent a room in conjunction with team day, board meeting or just a party?<br>Here is your opportunity to rent a place in an inspiring setting in the heart of Aalborg and overlooking the Limfjord from the roof terrace. We are happy to help you tailor an event that suits your needs and wishes. Contact us and we will find the right composition for you.</p>
  <p class="abs tagline">Your opportunity to drain into the entrepreneurial spirit</p>

  <div class="abs frame-band"></div>
  <div class="abs event-photo" role="img" aria-label="Photo of a wooden table with a potted plant, candles and a bowl of sweets in the event canteen"></div>

  <h3 class="abs prices-title">Indicative Prices</h3>
  <div class="abs prices-rule"></div>
  <ul class="abs price-list">
    <li><svg viewBox="0 0 10 10"><circle cx="5" cy="5" r="5" fill="#b5121b"/><path d="M2.6 5.2l1.6 1.6 3.2-3.4" stroke="#fff" stroke-width="1.4" fill="none"/></svg>Day event; The canteen and lounge area incl. catering: 400, - per envelope ex VAT.</li>
    <li><svg viewBox="0 0 10 10"><circle cx="5" cy="5" r="5" fill="#b5121b"/><path d="M2.6 5.2l1.6 1.6 3.2-3.4" stroke="#fff" stroke-width="1.4" fill="none"/></svg>Rent of the canteen: 5000, - ex moms</li>
    <li><svg viewBox="0 0 10 10"><circle cx="5" cy="5" r="5" fill="#b5121b"/><path d="M2.6 5.2l1.6 1.6 3.2-3.4" stroke="#fff" stroke-width="1.4" fill="none"/></svg>Rent of the lounge: 3000, - ex moms</li>
    <li><svg viewBox="0 0 10 10"><circle cx="5" cy="5" r="5" fill="#b5121b"/><path d="M2.6 5.2l1.6 1.6 3.2-3.4" stroke="#fff" stroke-width="1.4" fill="none"/></svg>If you need to rent the premises for a shorter period or in the evening hours, the hourly rate is 475, - ex VAT.</li>
  </ul>
  <div class="abs quote">
    <svg width="22" height="22" viewBox="0 0 22 22"><circle cx="11" cy="11" r="10" fill="none" stroke="#b5121b" stroke-width="1.2"/><path d="M8 6.5l1.6 1.8-.9 1.3c.6 1.4 1.6 2.4 3 3l1.3-.9 1.8 1.6-1 1.3c-3 0-6.1-3.1-6.1-6.1z" fill="#b5121b"/></svg>
    <span>Contact us for a quote on phone number: <span class="quote-phone">20 41 73 96</span></span>
  </div>

  <div class="abs cta-band"></div>
  <div class="abs btn-home">GO TO HOME PAGE</div>
</main>

<footer>
  <section class="abs contact" role="img" aria-label="Red-tinted group photo of the co-working community"></section>
  <p class="abs contact-heading">Do you need co-working space,<br>have a question or comment?</p>
  <div class="abs btn-info">GET MORE INFO</div>
  <div class="abs contact-divider"></div>

  <h4 class="abs col-title visit-title">Visit us</h4>
  <ul class="abs visit-list">
    <li><svg viewBox="0 0 10 10"><path d="M5 0.5a3.2 3.2 0 0 0-3.2 3.2C1.8 6 5 9.5 5 9.5S8.2 6 8.2 3.7A3.2 3.2 0 0 0 5 .5zm0 4.4a1.2 1.2 0 1 1 0-2.4 1.2 1.2 0 0 1 0 2.4z" fill="#fff"/></svg><span>NorvelHub fmba.Havnegade 14<br>9000 Aalborg, Denmark</span></li>
    <li><svg viewBox="0 0 10 10"><path d="M2 1l2 2-1 1.4c.7 1.4 1.3 2 2.6 2.6L7 6l2 2-1.2 1.4C4.5 9.4.6 5.5.6 2.2z" fill="#fff"/></svg><span>Call us: (+45) 20 41 73 96</span></li>
    <li><svg viewBox="0 0 10 10"><rect x=".5" y="2" width="9" height="6.5" fill="#fff"/><path d="M.5 2L5 5.6 9.5 2" stroke="#a90e16" stroke-width=".9" fill="none"/></svg><span>Email us: info@norvelhub.dk</span></li>
  </ul>

  <h4 class="abs col-title hours-title">Opening Hours</h4>
  <p class="abs hours-text">For residents: 24-7, all weekdays.<br>For guests: 9: 00-16: 00,<br>Monday-Friday.</p>

  <div class="abs base"></div>
  <nav class="abs foot-nav"><span>Home</span><span>Residents</span><span>Our Working Space</span><span>Our Event Space</span><span>Contact Us</span></nav>
  <div class="abs foot-rule"></div>
  <p class="abs copyright">Copyright © 2018. NorvelHub. All rights reserved.</p>
  <div class="abs brand brand-foot">NORVELHUB</div>
  <div class="abs social" aria-label="Social media links"><span></span><span></span><span></span><span></span><span></span></div>
</footer>

</body>
</html>
```